Redesign a Start-Up Dating Website

Website: https://morvelique.com.
Make sure the design has an island style theme.
I would like the 7 pages of my website to have a new and professional look. I want the same colors to remain, but I want a creative look for all the pages. This is a dating website that is in the startup stage. So, I want to give my entire website a custom makeover. I want something that will stand out from the other dating sites. Something that will attract more people to want to use my services, and hopefully get new members.
Target Market(s)
Dating
Industry/Entity Type
Dating
Coding
Coded - Design and coding required
Number of Pages Required
5+ page
Font styles to use
Other font styles liked:
- Decorative, San Serif
Requirements
Must have
- The design must have the original colors and a stylish font to go along. The design must be creative, welcoming, and professional. I would like an island style theme for the website. This is a dating website so make sure that the design is tailored to that aspect.
Nice to have
- It would be nice to have a decorative font and a professional style on all the pages. Make sure the design will be mobile responsive and friendly for all the pages on the website.
Should not have
- The design should not be bland and uncreative.

```html
<!DOCTYPE html>
<html lang="en">
<head>
<meta charset="utf-8">
<title>Morvelique — Find Your Match</title>
<link rel="stylesheet" href="https://fonts.googleapis.com/css2?family=Roboto:wght@300;400;500;700&family=Roboto+Condensed:wght@700&display=swap">
<style>
:root{
  --brand:#5aa88f;
  --purple:#6a4a9c;
  --purple-dark:#4e3578;
  --orange:#f5a000;
  --orange-dark:#e08c00;
  --ink:#222;
  --muted:#666;
  --teal:#2d8f72;
  --teal-dark:#1f6f57;
  --footer:#232323;
  --white:#fff;
}
*{box-sizing:border-box;margin:0;padding:0}
html,body{width:1200px;height:3056px;overflow:hidden}
body{font-family:"Roboto",Arial,sans-serif;color:var(--ink);background:var(--white);position:relative}
a{color:inherit;text-decoration:none}

/* Header */
.site-header{position:absolute;top:0;left:0;width:1200px;height:98px;display:flex;align-items:center;padding:0 90px;background:var(--white)}
.brand{display:flex;align-items:center;gap:12px;font-size:36px;font-weight:700;color:var(--brand)}
.brand-dot{width:52px;height:52px;border-radius:50%;background:var(--brand)}
.main-nav{margin-left:auto;display:flex;align-items:center;gap:36px;font-size:16px;color:#333}
.main-nav .active{color:var(--purple)}
.login-btn{background:var(--orange);color:var(--white);padding:10px 18px;border-radius:3px;font-size:15px;font-weight:500}

/* Hero */
.hero{position:absolute;top:98px;left:0;width:1200px;height:611px;background:linear-gradient(120deg,#6f8f4a 0%,#a7b98a 35%,#d9cbb8 55%,#8d9a7a 80%,#5b6e4a 100%)}
.hero-arrow{position:absolute;top:308px;width:36px;height:36px;border-radius:50%;background:rgba(0,0,0,.55)}
.hero-arrow svg{display:block;margin:9px auto}
.hero-arrow.prev{left:30px}.hero-arrow.next{right:30px}
.match-form{position:absolute;left:112px;top:116px;width:364px;height:411px;background:rgba(106,74,156,.88);border:7px solid var(--white);box-shadow:0 4px 14px rgba(0,0,0,.3);padding:26px 40px}
.match-form h2{color:var(--white);font-size:22px;font-weight:400;text-align:center;padding-bottom:14px;border-bottom:1px solid rgba(255,255,255,.4);margin-bottom:22px}
.form-row{display:flex;align-items:center;justify-content:flex-end;margin-bottom:10px}
.form-row label{color:var(--white);font-size:14px;width:80px}
.select{width:200px;height:36px;background:var(--white);border-radius:2px;position:relative}
.select::after{content:"";position:absolute;right:12px;top:15px;border:5px solid transparent;border-top-color:#777}
.search-btn{display:block;margin:20px auto 0;width:112px;height:36px;background:#111;color:var(--white);border:none;font-size:14px;font-family:inherit}
.hero-tagline{position:absolute;right:110px;top:435px;text-align:right;font-family:"Roboto Condensed",Arial,sans-serif;color:var(--white);font-size:29px;line-height:41px;text-transform:uppercase;text-shadow:0 2px 4px rgba(0,0,0,.5)}

/* Welcome */
.welcome{position:absolute;top:709px;left:0;width:1200px;text-align:center}
.welcome h1{margin-top:92px;font-size:32px;font-weight:400;color:var(--ink)}
.welcome .intro{width:960px;margin:26px auto 0;font-size:14.5px;line-height:25px;color:var(--muted)}
.steps{display:flex;justify-content:center;gap:0;margin-top:58px}
.step{width:334px;text-align:center}
.step-icon{width:92px;height:92px;margin:0 auto;border:1.5px solid #999;border-radius:50%;display:flex;align-items:center;justify-content:center}
.step h3{margin-top:24px;font-size:19px;font-weight:400}
.step p{width:260px;margin:12px auto 0;font-size:13.5px;line-height:21px;color:var(--muted)}

/* Dating easy band */
.easy{position:absolute;top:1355px;left:0;width:1200px;height:352px;background:linear-gradient(90deg,#f4f4f4,#eceae8 50%,#f2f2f2)}
.easy-couple{position:absolute;left:34px;top:-133px;width:450px;height:485px;background:linear-gradient(160deg,#c99a7a 0%,#5f8fc0 45%,#3d6fa6 80%,#e8365a 100%);border-radius:200px 200px 0 0}
.easy-copy{position:absolute;left:516px;top:100px}
.easy-copy h2{font-size:31px;font-weight:500;color:var(--ink)}
.easy-copy p{font-size:20px;color:#555;margin-top:12px;line-height:26px}
.trial-btn{display:inline-block;margin-top:22px;background:var(--purple);color:var(--white);font-size:15px;padding:14px 22px;border-radius:3px}

/* Community */
.community{position:absolute;top:1707px;left:0;width:1200px;height:534px;background:radial-gradient(ellipse at 55% 40%,#3ea383 0%,var(--teal) 45%,var(--teal-dark) 100%);text-align:center;color:var(--white)}
.community h2{margin-top:80px;font-size:30px;font-weight:400}
.members{display:flex;justify-content:center;margin-top:60px}
.member{width:258px}
.member-photo{width:126px;height:126px;margin:0 auto;border-radius:50%;border:4px solid var(--white);background:linear-gradient(180deg,#c9d6e0,#7f9bb3)}
.member h3{margin-top:18px;font-size:18px;font-weight:700}
.member p{width:190px;margin:10px auto 0;font-size:14px;line-height:22px}
.member-social{display:flex;justify-content:center;gap:8px;margin-top:14px}
.member-social span{width:16px;height:16px;border-radius:3px;background:var(--white)}
.member-contact{display:block;margin-top:8px;font-size:12px;font-weight:500}

/* Benefits */
.benefits{position:absolute;top:2241px;left:0;width:1200px;text-align:center}
.benefits-badge{width:60px;height:60px;margin:76px auto 0;border-radius:50%;background:var(--brand)}
.benefits h2{margin-top:22px;font-size:30px;font-weight:500}
.benefits p{margin-top:26px;font-size:20px;color:#555}
.plans-btn{display:inline-block;margin-top:22px;background:linear-gradient(180deg,var(--orange),var(--orange-dark));color:var(--white);font-size:16px;font-weight:500;padding:14px 26px;border-radius:3px}

/* Footer */
.site-footer{position:absolute;top:2628px;left:0;width:1200px;height:428px;background:linear-gradient(135deg,#2a2a2a,var(--footer) 50%,#1c1c1c);color:var(--white)}
.subscribe{position:absolute;left:178px;top:60px;display:flex;align-items:center}
.subscribe h3{font-size:25px;font-weight:400;width:290px}
.subscribe-field{width:348px;height:44px;background:var(--white);border-radius:22px 0 0 22px;color:#999;font-size:13px;line-height:44px;padding-left:22px}
.subscribe-btn{height:44px;width:96px;background:#2aa38a;border-radius:0 22px 22px 0;font-size:13px;line-height:44px;text-align:center}
.footer-rule{position:absolute;left:95px;right:95px;height:1px;background:rgba(255,255,255,.15)}
.footer-cols{position:absolute;top:184px;left:97px;display:flex}
.footer-col h4{font-size:14px;font-weight:500;margin-bottom:16px}
.footer-col li{list-style:none;font-size:12.5px;line-height:23px}
.footer-col li::before{content:"» ";}
.footer-col.info{width:276px}.footer-col.links{width:243px}.footer-col.contact{width:322px}
.contact-lines{font-size:12.5px;line-height:23px}
.social-dots{display:flex;gap:10px}
.social-dots span{width:30px;height:30px;border-radius:50%;background:var(--white)}
.copyright{position:absolute;bottom:36px;width:100%;text-align:center;font-size:12.5px}
</style>
</head>
<body>

<header class="site-header">
  <a class="brand" href="https://morvelique.com"><span class="brand-dot"></span>Morvelique</a>
  <nav class="main-nav">
    <a class="active" href="#">Home</a><a href="#">Search</a><a href="#">Members</a><a href="#">Extras</a><a href="#">About</a><a href="#">Premium</a><a href="#">Contact</a>
    <a class="login-btn" href="#">LOGIN ▾</a>
  </nav>
</header>

<section class="hero" role="img" aria-label="Photo of a smiling couple sitting on a park bench among trees">
  <span class="hero-arrow prev"><svg width="18" height="18" viewBox="0 0 18 18"><path d="M11 3 5 9l6 6" stroke="#fff" stroke-width="2.5" fill="none"/></svg></span>
  <span class="hero-arrow next"><svg width="18" height="18" viewBox="0 0 18 18"><path d="m7 3 6 6-6 6" stroke="#fff" stroke-width="2.5" fill="none"/></svg></span>
  <form class="match-form">
    <h2>FIND YOUR MATCH</h2>
    <div class="form-row"><label>I'am</label><div class="select"></div></div>
    <div class="form-row"><label>Seeking a</label><div class="select"></div></div>
    <div class="form-row"><label>Age from</label><div class="select"></div></div>
    <div class="form-row"><label>AgeTo</label><div class="select"></div></div>
    <div class="form-row"><label>Country</label><div class="select"></div></div>
    <button class="search-btn" type="button">SEARCH</button>
  </form>
  <p class="hero-tagline">Let's find your perfect match today<br>Find your perfect match for free!</p>
</section>

<section class="welcome">
  <h1>WELCOME TO MORVELIQUE</h1>
  <p class="intro">Lorem Ipsum has been the industry's standard dummy text ever since the 1500s, when an unknown printer took a galley of type and scrambled it to make a type specimen book. It has survived not only five centuries, but also the leap into electronic typesetting, remaining essentially unchanged. It was popularised in the 1960s with the release of Typoset sheets containing Lorem Pagewright Studio including versions</p>
  <div class="steps">
    <div class="step">
      <div class="step-icon"><svg width="34" height="34" viewBox="0 0 34 34"><rect x="4" y="6" width="22" height="24" rx="4" fill="none" stroke="#f5a000" stroke-width="2.5"/><path d="m14 20 2-5 12-12 3 3-12 12z" fill="#f5a000"/></svg></div>
      <h3>CREATE A PROFILE</h3>
      <p>Let people know all about you; the good and the quirky-show the world your true colors and find someone</p>
    </div>
    <div class="step">
      <div class="step-icon"><svg width="30" height="34" viewBox="0 0 30 34"><circle cx="15" cy="9" r="7" fill="#f5a000"/><path d="M2 32c0-9 6-14 13-14s13 5 13 14z" fill="#f5a000"/></svg></div>
      <h3>FIND MATCHES</h3>
      <p>Let people know all about you; the good and the quirky-show the world your true colors and find someone</p>
    </div>
    <div class="step">
      <div class="step-icon"><svg width="32" height="34" viewBox="0 0 32 34"><rect x="3" y="6" width="26" height="25" rx="2" fill="none" stroke="#f5a000" stroke-width="2.5"/><path d="M3 12h26M10 2v7M22 2v7" stroke="#f5a000" stroke-width="2.5"/><path d="M8 17h4v3H8zm7 0h4v3h-4zm7 0h3v3h-3zM8 23h4v3H8zm7 0h4v3h-4z" fill="#f5a000"/></svg></div>
      <h3>START DATING</h3>
      <p>Let people know all about you; the good and the quirky-show the world your true colors and find someone</p>
    </div>
  </div>
</section>

<section class="easy" role="img" aria-label="Faint collage of member portraits behind the section">
  <div class="easy-couple" role="img" aria-label="Photo of a smiling couple in denim shirts holding a red paper heart"></div>
  <div class="easy-copy">
    <h2>DATING IS EASY WITH MORVELIQUE</h2>
    <p>Sign-up for a 30 days free trial</p>
    <p>Enjoy all the benefits morvelique has to offer with a full membership.</p>
    <a class="trial-btn" href="#">Start Morveliquing with Free Sign-Up</a>
  </div>
</section>

<section class="community" role="img" aria-label="Soft green-tinted photo of a couple as section background">
  <h2>JOIN THIS COMMUNITY OF &nbsp;1 MORVELIQUE MEMBERS</h2>
  <div class="members">
    <div class="member"><div class="member-photo" role="img" aria-label="Member portrait photo"></div><h3>Neque quisquam</h3><p>Lorem Ipsum has been the industry's standard dummy</p><div class="member-social"><span></span><span></span><span></span><span></span></div><a class="member-contact" href="#">CONTACT »</a></div>
    <div class="member"><div class="member-photo" role="img" aria-label="Member portrait photo"></div><h3>Dolorem Ipsum</h3><p>Lorem Ipsum has been the industry's standard dummy</p><div class="member-social"><span></span><span></span><span></span><span></span></div><a class="member-contact" href="#">CONTACT »</a></div>
    <div class="member"><div class="member-photo" role="img" aria-label="Member portrait photo"></div><h3>Neque quisquam</h3><p>Lorem Ipsum has been the industry's standard dummy</p><div class="member-social"><span></span><span></span><span></span><span></span></div><a class="member-contact" href="#">CONTACT »</a></div>
    <div class="member"><div class="member-photo" role="img" aria-label="Member portrait photo"></div><h3>Dolorem Ipsum</h3><p>Lorem Ipsum has been the industry's standard dummy</p><div class="member-social"><span></span><span></span><span></span><span></span></div><a class="member-contact" href="#">CONTACT »</a></div>
  </div>
</section>

<section class="benefits">
  <div class="benefits-badge"></div>
  <h2>BENEFITS</h2>
  <p>Affordable Easy sign-up and cancellation processes</p>
  <a class="plans-btn" href="#">View Membership Plans</a>
</section>

<footer class="site-footer">
  <div class="subscribe">
    <h3>Subscribe for Updates</h3>
    <div class="subscribe-field">email@example.com</div>
    <div class="subscribe-btn">SUBSCRIBE</div>
  </div>
  <div class="footer-rule" style="top:148px"></div>
  <div class="footer-cols">
    <div class="footer-col info"><h4>INFORMATION</h4><ul><li>Privacy Policy</li><li>Login</li><li>Register</li><li>Contact Us</li></ul></div>
    <div class="footer-col links"><h4>LINKS</h4><ul><li>Home</li><li>Search</li><li>Members</li><li>Extras</li></ul></div>
    <div class="footer-col contact"><h4>CONTACT US</h4><div class="contact-lines">Address : Morvelique<br>Coral Bay, Palm Harbor Isles, 00931<br>Phone : &nbsp;(844) 555-0172<br>Email : &nbsp;contact@morvelique.com</div></div>
    <div class="footer-col follow"><h4>FOLLOW US OUT THERE</h4><div class="social-dots"><span></span><span></span><span></span></div></div>
  </div>
  <div class="footer-rule" style="top:340px"></div>
  <p class="copyright">Copyright © 2017. All Rights Reserved</p>
</footer>

</body>
</html>
```